QP Fiduciary Website Redesign Contest

We want to refresh our website to be more insitutional, professional for an international audience. We have designed a new logo for this purpose and that has been attached. A full brand brief and positioning statement has also been attached. Please read through all the documents carefully before designing. The old website is found here: https://qp-fiduciary.example/

Target Market(s)

Actuaries and associated businesses internationally

Industry/Entity Type

professional services - actuaries

Number of Pages Required

3 page

Font styles to use
Sans Serif

Colors
0054AA
0677BA
7BADD7
CADEEF
E8F1F8
0094D4
00A9DD
6FCCEA
C7EBF8
E9F6FB
F0912C
F2A743
F7CA91
FBE8D2
FDF5EE
EE7325
F08F49
F5BC92
FAE3D3
FDF4ED
EB3D1F
EC4F4E
F09395
F8D3D4
FCEDEE

Requirements
Must have
• blues and greens to match the logo color, complimentary colors, navigation
Nice to have
• old site: https://qp-fiduciary.example/

```html
<!DOCTYPE html>
<html lang="en">
<head>
<meta charset="utf-8">
<title>QP Fiduciary — Actuarial Software</title>
<link href="https://fonts.googleapis.com/css2?family=Orbitron:wght@400;800&family=Inter:wght@400;500;600;700&display=swap" rel="stylesheet">
<style>
:root{
  --primary:#0677BA;
  --primary-deep:#0054AA;
  --sky:#00A9DD;
  --sky-mid:#0094D4;
  --sky-soft:#7BADD7;
  --tint:#CADEEF;
  --tint-light:#E8F1F8;
  --ink:#13233A;
  --text:#3C4656;
  --muted:#5E6877;
  --grey-bg:#F0F5FA;
  --navy:#0B2542;
  --navy-line:#24405F;
  --white:#fff;
}
*{margin:0;padding:0;box-sizing:border-box}
html,body{width:1200px;height:4098px;overflow:hidden}
body{position:relative;font-family:"Inter",Arial,sans-serif;color:var(--text);background:var(--white)}
section,header,footer{position:absolute;left:0;width:1200px}
.section-title{position:absolute;left:0;width:100%;text-align:center;font-family:"Orbitron",Arial,sans-serif;font-weight:800;font-size:34px;color:var(--ink);letter-spacing:1px}
.section-title span{color:var(--primary)}
.title-rule{position:absolute;left:578px;width:44px;height:2px;background:var(--sky)}
.section-sub{position:absolute;left:0;width:100%;text-align:center;font-size:14px;line-height:23px;color:var(--text)}
.btn{position:absolute;display:flex;align-items:center;justify-content:space-between;background:var(--primary);color:var(--white);font-size:14px;font-weight:500;border-radius:24px;padding:0 6px 0 24px;text-decoration:none;white-space:nowrap}
.btn .arrow{width:32px;height:32px;border-radius:50%;border:2px solid var(--white);display:flex;align-items:center;justify-content:center}
.learn{font-size:12.5px;color:var(--primary-deep);display:flex;align-items:center;gap:14px}

/* header */
.site-header{top:0;height:70px;background:var(--white)}
.brand{position:absolute;display:flex;align-items:center;gap:10px;font-family:"Inter",Arial,sans-serif;font-weight:600;letter-spacing:2px;white-space:nowrap}
.brand .dot{width:14px;height:14px;border-radius:50%;background:var(--sky)}
.site-header .brand{left:70px;top:20px;font-size:24px;color:var(--primary-deep)}
.nav{position:absolute;top:27px;font-size:13px;color:var(--text)}
.nav.active{color:var(--primary)}

/* hero */
.hero{top:70px;height:544px}
.hero-photo{position:absolute;inset:0;background:linear-gradient(90deg,#1a2633 0%,#33404c 40%,#8d939a 65%,#6b7077 100%)}
.hero-shade{position:absolute;inset:0;background:linear-gradient(90deg,rgba(5,25,50,.6) 0%,rgba(5,25,50,.3) 50%,rgba(0,0,0,0) 75%)}
.hero h1{position:absolute;left:70px;top:121px;font-family:"Orbitron",Arial,sans-serif;font-size:31px;line-height:42px;color:var(--white);font-weight:400;letter-spacing:1px}
.hero h1 b{font-weight:800}
.hero p{position:absolute;left:72px;top:302px;width:480px;font-size:14px;line-height:23px;color:var(--white)}

/* overview */
.overview{top:614px;height:553px}
.feature-card{position:absolute;top:212px;width:214px;height:256px;background:var(--white);border-radius:8px;box-shadow:0 2px 14px rgba(6,60,120,.09)}
.feature-card svg{position:absolute;left:22px;top:26px}
.feature-card h3{position:absolute;left:22px;top:104px;width:170px;font-size:15px;line-height:21px;color:var(--ink);font-weight:600}
.feature-card .rule{position:absolute;left:22px;top:153px;width:30px;height:2px;background:var(--sky)}
.feature-card p{position:absolute;left:22px;top:172px;width:160px;font-size:12.5px;line-height:19px;color:var(--muted)}

/* core */
.core{top:1167px;height:682px;background:var(--grey-bg)}
.core-photo{position:absolute;left:142px;top:197px;width:423px;height:399px;border-radius:10px;background:linear-gradient(135deg,#e3e8ec 0%,#bcc4cb 45%,#2f3a44 80%,#1a222a 100%)}
.solution{position:absolute;left:629px;width:430px}
.solution .badge{position:absolute;left:0;top:0;width:72px;height:72px;border-radius:50%;display:flex;align-items:center;justify-content:center}
.solution h3{position:absolute;left:92px;top:0;font-size:15px;font-weight:600;color:var(--ink)}
.solution p{position:absolute;left:92px;top:24px;width:335px;font-size:12.5px;line-height:19px;color:var(--muted)}
.solution .learn{position:absolute;left:92px;top:90px}
.bg-deep{background:var(--primary-deep)}
.bg-sky{background:var(--sky)}

/* characteristics */
.traits{top:1849px;height:729px}
.ring{position:absolute;left:425px;top:204px}
.ring-brand{position:absolute;left:0;width:1200px;top:364px;display:flex;justify-content:center}
.ring-brand .brand{position:static;font-size:26px;color:var(--primary-deep)}
.trait-icon{position:absolute;width:76px;height:76px;border-radius:50%;display:flex;align-items:center;justify-content:center}
.trait{position:absolute;width:260px}
.trait h3{font-size:15px;font-weight:600;color:var(--ink);margin-bottom:6px}
.trait p{font-size:12.5px;line-height:19px;color:var(--muted)}
.trait.left{text-align:right}

/* insights */
.insights{top:2578px;height:681px;background:var(--grey-bg)}
.post{position:absolute;top:150px;width:286px;height:366px;background:var(--white);border-radius:8px;overflow:hidden;box-shadow:0 2px 12px rgba(6,60,120,.06)}
.post .thumb{height:191px}
.post h3{position:absolute;left:19px;top:210px;width:250px;font-size:15px;line-height:21px;font-weight:600;color:var(--ink)}
.post p{position:absolute;left:19px;top:260px;width:250px;font-size:12.5px;line-height:19px;color:var(--muted)}
.post .learn{position:absolute;left:19px;top:328px}

/* cta */
.cta-band{top:3259px;height:500px;background:linear-gradient(180deg,var(--white) 0 357px,var(--navy) 357px)}
.cta-box{position:absolute;left:142px;top:86px;width:916px;height:376px;border-radius:24px;overflow:hidden;background:radial-gradient(circle at 28% 22%,#1d5b8c 0%,#0f2d4c 38%,#07131f 78%)}
.cta-box h2{position:absolute;left:0;width:100%;top:90px;text-align:center;font-family:"Orbitron",Arial,sans-serif;color:var(--white);font-size:33px;line-height:42px;font-weight:400;letter-spacing:1px}
.cta-box h2 b{font-weight:800}
.cta-box p{position:absolute;left:0;width:100%;top:183px;text-align:center;font-size:14px;line-height:23px;color:var(--white)}

/* footer */
.site-footer{top:3759px;height:339px;background:var(--navy);color:var(--tint)}
.site-footer .brand{left:142px;top:58px;font-size:30px;color:var(--white)}
.foot-desc{position:absolute;left:142px;top:134px;width:300px;font-size:12.5px;line-height:19px;color:var(--tint)}
.foot-title{position:absolute;top:58px;font-family:"Orbitron",Arial,sans-serif;font-size:15px;color:var(--white);letter-spacing:1px}
.foot-links{position:absolute;left:576px;top:102px;list-style:none;font-size:12.5px;line-height:27px;color:var(--tint)}
.contact{position:absolute;left:813px;display:flex;gap:12px;font-size:12.5px;line-height:19px;color:var(--tint)}
.contact strong{font-weight:600;color:var(--white);font-size:13px}
.foot-rule{position:absolute;left:142px;top:288px;width:916px;height:1px;background:var(--navy-line)}
.foot-bottom{position:absolute;left:142px;top:305px;font-size:12px;color:var(--tint)}
.social{position:absolute;top:298px;width:32px;height:32px;border-radius:50%;border:1.5px solid var(--white)}
.social.filled{background:var(--white)}
</style>
</head>
<body>

<header class="site-header">
  <div class="brand"><span class="dot"></span>QP FIDUCIARY</div>
  <span class="nav active" style="left:390px">Home</span>
  <span class="nav" style="left:462px">Platform</span>
  <span class="nav" style="left:544px">Solutions</span>
  <span class="nav" style="left:632px">Insights</span>
  <span class="nav" style="left:711px">Company</span>
  <span class="nav" style="left:802px">Contact</span>
  <a class="btn" style="left:882px;top:16px;width:248px;height:38px;justify-content:center;padding:0;font-size:13px">Request a Technical Walkthrough</a>
</header>

<section class="hero">
  <div class="hero-photo" role="img" aria-label="Photo of two smiling colleagues reviewing charts at an office desk with a laptop and coffee cup"></div>
  <div class="hero-shade"></div>
  <h1>ACTUARIAL SOFTWARE<br>FOR <b>STRUCTURED,</b><br><b>AUDITABLE FINANCIAL</b><br><b>ANALYSIS.</b></h1>
  <p><b>QP Fiduciary</b> develops software that translates established actuarial methodologies into disciplined, decision-ready tools.</p>
  <a class="btn" style="left:70px;top:374px;width:302px;height:44px">Request A Technical Walkthrough<span class="arrow"><svg width="14" height="14" viewBox="0 0 14 14"><path d="M1 7h11M8 3l4 4-4 4" stroke="#fff" stroke-width="1.8" fill="none"/></svg></span></a>
</section>

<section class="overview">
  <h2 class="section-title" style="top:68px">PLATFORM <span>OVERVIEW</span></h2>
  <div class="title-rule" style="top:121px"></div>
  <p class="section-sub" style="top:140px">Our platform empowers actuaries and risk professionals with tools designed for modern<br>regulatory and business demands.</p>

  <div class="feature-card" style="left:142px">
    <svg width="52" height="52" viewBox="0 0 52 52"><rect x="4" y="6" width="40" height="36" rx="3" fill="#CADEEF"/><rect x="2" y="4" width="40" height="36" rx="3" fill="none" stroke="#0054AA" stroke-width="1.8"/><circle cx="22" cy="16" r="4" fill="none" stroke="#0054AA" stroke-width="1.8"/><path d="M22 20v6M10 32v-6h24v6M22 26v6" stroke="#0054AA" stroke-width="1.8" fill="none"/></svg>
    <h3>Structured Workflows</h3><div class="rule"></div>
    <p>that guide users through every step of the analysis process</p>
  </div>
  <div class="feature-card" style="left:376px">
    <svg width="52" height="52" viewBox="0 0 52 52"><circle cx="26" cy="24" r="18" fill="#C7EBF8"/><circle cx="24" cy="22" r="18" fill="none" stroke="#0094D4" stroke-width="1.8"/><path d="M12 30l20-20M10 22l14-14M16 36l22-22" stroke="#0094D4" stroke-width="1.6"/></svg>
    <h3>Full Transparency Of Assumptions</h3><div class="rule"></div>
    <p>that guide users through every step of the analysis process</p>
  </div>
  <div class="feature-card" style="left:610px">
    <svg width="52" height="52" viewBox="0 0 52 52"><rect x="6" y="4" width="28" height="38" rx="2" fill="none" stroke="#0054AA" stroke-width="1.8"/><path d="M11 12h16M11 18h12M11 24h10" stroke="#0054AA" stroke-width="1.8"/><circle cx="32" cy="30" r="9" fill="#CADEEF" stroke="#0054AA" stroke-width="1.8"/><path d="M39 37l7 7" stroke="#0054AA" stroke-width="2.4"/></svg>
    <h3>Built-in Auditability</h3><div class="rule"></div>
    <p>that guide users through every step of the analysis process</p>
  </div>
  <div class="feature-card" style="left:843px">
    <svg width="52" height="52" viewBox="0 0 52 52"><circle cx="24" cy="24" r="20" fill="#C7EBF8" stroke="#0094D4" stroke-width="1.8"/><path d="M14 20l10-6 10 6zM16 22v10M21 22v10M27 22v10M32 22v10M13 34h22" stroke="#0094D4" stroke-width="1.8" fill="none"/></svg>
    <h3>Robust Governance Features</h3><div class="rule"></div>
    <p>that guide users through every step of the analysis process</p>
  </div>
</section>

<section class="core">
  <h2 class="section-title" style="top:72px">CORE <span>SOLUTIONS</span></h2>
  <div class="title-rule" style="top:123px"></div>
  <p class="section-sub" style="top:141px">Precision-built modules for the most demanding actuarial tasks</p>
  <div class="core-photo" role="img" aria-label="Photo of two hands joining wooden puzzle pieces"></div>

  <div class="solution" style="top:197px">
    <div class="badge bg-deep"><svg width="38" height="38" viewBox="0 0 38 38" fill="none" stroke="#fff" stroke-width="1.8"><circle cx="20" cy="13" r="8"/><path d="M20 5v8h8M4 28l6-4h10l-6 4M10 32h14l10-8"/></svg></div>
    <h3>Reserving &amp; Valuation</h3>
    <p>Perform compliant, repeatable reserving and valuation processes with full traceability and support for multiple actuarial methods and regulatory frameworks.</p>
    <span class="learn">Learn More <svg width="16" height="10" viewBox="0 0 16 10"><path d="M0 5h14M10 1l4 4-4 4" stroke="#0054AA" stroke-width="1.4" fill="none"/></svg></span>
  </div>
  <div class="solution" style="top:345px">
    <div class="badge bg-sky"><svg width="38" height="38" viewBox="0 0 38 38" fill="none" stroke="#fff" stroke-width="1.8"><path d="M8 4h16l6 6v14M8 4v30h14"/><circle cx="27" cy="28" r="7"/><path d="M27 24v8M25 26h3a1.5 1.5 0 010 3h-2"/><path d="M12 14h10M12 19h8"/></svg></div>
    <h3>Pricing</h3>
    <p>Build and test pricing models with transparent assumptions, scenario testing, and comparative analytics to support profitable product development.</p>
    <span class="learn">Learn More <svg width="16" height="10" viewBox="0 0 16 10"><path d="M0 5h14M10 1l4 4-4 4" stroke="#0054AA" stroke-width="1.4" fill="none"/></svg></span>
  </div>
  <div class="solution" style="top:493px">
    <div class="badge bg-deep"><svg width="38" height="38" viewBox="0 0 38 38" fill="none" stroke="#fff" stroke-width="1.8"><circle cx="19" cy="16" r="11"/><path d="M19 9l5 10H14zM19 13v3M4 30l6-3h10l-5 3M10 34h14l10-7"/></svg></div>
    <h3>Enterprise Risk Management</h3>
    <p>Integrate risk metrics, stress testing, and capital modeling in a governed environment to support ORSA, Solvency II, and other ERM requirements.</p>
    <span class="learn">Learn More <svg width="16" height="10" viewBox="0 0 16 10"><path d="M0 5h14M10 1l4 4-4 4" stroke="#0054AA" stroke-width="1.4" fill="none"/></svg></span>
  </div>
</section>

<section class="traits">
  <h2 class="section-title" style="top:68px">PLATFORM <span>CHARACTERISTICS</span></h2>
  <div class="title-rule" style="top:122px"></div>
  <p class="section-sub" style="top:142px">Engineered for clarity, built to scale across borders</p>

  <svg class="ring" width="350" height="350" viewBox="0 0 350 350"><circle cx="175" cy="175" r="172" fill="none" stroke="#7BADD7" stroke-width="2"/></svg>
  <div class="ring-brand"><div class="brand"><span class="dot"></span>QP FIDUCIARY</div></div>

  <div class="trait-icon bg-deep" style="left:444px;top:226px"><svg width="36" height="36" viewBox="0 0 36 36" fill="none" stroke="#fff" stroke-width="1.7"><rect x="13" y="3" width="10" height="8" rx="1"/><path d="M18 11v6M6 24v-7h24v7M18 17v7"/><rect x="2" y="24" width="8" height="7" rx="1"/><rect x="14" y="24" width="8" height="7" rx="1"/><rect x="26" y="24" width="8" height="7" rx="1"/></svg></div>
  <div class="trait-icon bg-sky" style="left:680px;top:226px"><svg width="36" height="36" viewBox="0 0 36 36" fill="none" stroke="#fff" stroke-width="1.7"><circle cx="12" cy="9" r="5"/><circle cx="24" cy="12" r="4"/><path d="M3 30l7-4h10l-5 3M9 34h14l10-7"/></svg></div>
  <div class="trait-icon bg-sky" style="left:444px;top:459px"><svg width="36" height="36" viewBox="0 0 36 36" fill="none" stroke="#fff" stroke-width="1.7"><path d="M6 3h16l6 6v24H6z"/><ellipse cx="17" cy="19" rx="8" ry="5"/><circle cx="17" cy="19" r="2"/></svg></div>
  <div class="trait-icon bg-deep" style="left:680px;top:459px"><svg width="36" height="36" viewBox="0 0 36 36" fill="none" stroke="#fff" stroke-width="1.7"><circle cx="18" cy="16" r="12"/><path d="M12 22v-6M17 22v-9M22 22v-4M4 32l8-6 6 4 12-8"/></svg></div>

  <div class="trait left" style="left:158px;top:243px"><h3>Structured Workflows</h3><p>Consistent, repeatable processes from<br>data to disclosure.</p></div>
  <div class="trait" style="left:781px;top:243px"><h3>Multi-jurisdictional Review Support</h3><p>Localise assumptions, outputs, and reports<br>for any regulator.</p></div>
  <div class="trait left" style="left:158px;top:476px"><h3>Transparent Assumptions</h3><p>Every assumption exposed, documented,<br>and linked to source.</p></div>
  <div class="trait" style="left:781px;top:476px"><h3>Comparative Analysis Capability</h3><p>Run scenarios side by side — instantly see<br>impacts.</p></div>

  <a class="btn" style="left:449px;top:597px;width:302px;height:45px">Request A Technical Walkthrough<span class="arrow"><svg width="14" height="14" viewBox="0 0 14 14"><path d="M1 7h11M8 3l4 4-4 4" stroke="#fff" stroke-width="1.8" fill="none"/></svg></span></a>
</section>

<section class="insights">
  <h2 class="section-title" style="top:72px">LATEST <span>INSIGHTS</span></h2>
  <div class="title-rule" style="top:124px"></div>

  <article class="post" style="left:142px">
    <div class="thumb" role="img" aria-label="Photo of hands using a calculator beside a laptop, charts and a potted plant" style="background:linear-gradient(135deg,#e9eef2,#9fb2c2 60%,#6f8798)"></div>
    <h3>Advancing Actuarial Methods in a Changing Regulatory Landscape</h3>
    <p>Exploring how modern tools support evolving best practices in reserving and capital modeling.</p>
    <span class="learn">Learn More <svg width="16" height="10" viewBox="0 0 16 10"><path d="M0 5h14M10 1l4 4-4 4" stroke="#0054AA" stroke-width="1.4" fill="none"/></svg></span>
  </article>
  <article class="post" style="left:457px">
    <div class="thumb" role="img" aria-label="Photo of printed financial charts being reviewed on a warm-toned desk" style="background:linear-gradient(135deg,#F5BC92,#F08F49 50%,#e4e1dc)"></div>
    <h3>Governance and Documentation in Actuarial Modeling</h3>
    <p>Why audit trails and assumption transparency are critical for internal and external review.</p>
    <span class="learn">Learn More <svg width="16" height="10" viewBox="0 0 16 10"><path d="M0 5h14M10 1l4 4-4 4" stroke="#0054AA" stroke-width="1.4" fill="none"/></svg></span>
  </article>
  <article class="post" style="left:772px">
    <div class="thumb" role="img" aria-label="Photo of a professional working on a laptop showing data charts in a dark office" style="background:linear-gradient(135deg,#2e3a44,#1b232a 60%,#3d5f4a)"></div>
    <h3>Multi-Jurisdictional Actuarial Practice: Challenges &amp; Solutions</h3>
    <p>Strategies for managing compliance across Solvency II, IARB, and emerging frameworks.</p>
    <span class="learn">Learn More <svg width="16" height="10" viewBox="0 0 16 10"><path d="M0 5h14M10 1l4 4-4 4" stroke="#0054AA" stroke-width="1.4" fill="none"/></svg></span>
  </article>

  <a class="btn" style="left:516px;top:553px;width:168px;height:44px">Read Insights<span class="arrow"><svg width="14" height="14" viewBox="0 0 14 14"><path d="M1 7h11M8 3l4 4-4 4" stroke="#fff" stroke-width="1.8" fill="none"/></svg></span></a>
</section>

<section class="cta-band">
  <div class="cta-box" role="img" aria-label="Dark photo of a hand holding a smartphone beneath a glowing digital globe">
    <h2>READY TO SEE THE<br><b>PLATFORM IN ACTION?</b></h2>
    <p>Schedule a technical walkthrough and discover how QP Fiduciary can bring<br>structure, transparency, and auditability to your actuarial processes.</p>
    <a class="btn" style="left:307px;top:245px;width:302px;height:45px">Request A Technical Walkthrough<span class="arrow"><svg width="14" height="14" viewBox="0 0 14 14"><path d="M1 7h11M8 3l4 4-4 4" stroke="#fff" stroke-width="1.8" fill="none"/></svg></span></a>
  </div>
</section>

<footer class="site-footer">
  <div class="brand"><span class="dot"></span>QP FIDUCIARY</div>
  <p class="foot-desc">Software that translates actuarial methodologies into disciplined decision-ready analytical tools across diverse regulatory environments.</p>

  <h4 class="foot-title" style="left:576px">QUICK LINKS</h4>
  <ul class="foot-links"><li>Home</li><li>Platform</li><li>Solutions</li><li>Insights</li><li>Company</li><li>Contact</li></ul>

  <h4 class="foot-title" style="left:813px">CONTACT DETAILS</h4>
  <div class="contact" style="top:98px"><svg width="16" height="18" viewBox="0 0 16 18"><path d="M8 17s6-6 6-10A6 6 0 002 7c0 4 6 10 6 10z" fill="#fff"/><circle cx="8" cy="7" r="2.2" fill="#0B2542"/></svg><div><strong>QP Fiduciary, Inc.</strong><br>418 Harbor Point Ave, Suite 210<br>Bayview, FL 33990</div></div>
  <div class="contact" style="top:176px"><svg width="16" height="16" viewBox="0 0 16 16"><path d="M3 1l3 3-2 2c1 2 3 4 5 5l2-2 3 3-2 3C7 15 1 9 1 3z" fill="#fff"/></svg><strong>+1(555)010-4827</strong></div>
  <div class="contact" style="top:215px"><svg width="16" height="14" viewBox="0 0 16 14"><rect x="0" y="1" width="16" height="12" rx="1.5" fill="#fff"/><path d="M1 2l7 6 7-6" stroke="#0B2542" stroke-width="1.4" fill="none"/></svg>hello@qp-fiduciary.example</div>

  <div class="foot-rule"></div>
  <p class="foot-bottom">© 2026 QP Fiduciary. All rights reserved.&nbsp;&nbsp;&nbsp;&nbsp;&nbsp;&nbsp;&nbsp;Privacy · Terms</p>
  <span class="social filled" style="left:947px"></span>
  <span class="social" style="left:987px"></span>
  <span class="social" style="left:1026px"></span>
</footer>

</body>
</html>
```